Business Card for Industrial Distributor

We need a business card design for an industrial distributor. We sell machine parts for the manufacturing and oil industry. We would like the cards to look clean and modern but with a touch of industry.

Our colors are blue/white.

Please feel free to visit our website www.korvelpartsco.com

Target Market(s)

mexican manufacturers in the automobile/aerospace industry

Industry/Entity Type

Industrial

Colors
ffffff
0555a3

```html
<!DOCTYPE html>
<html lang="en">
<head>
<meta charset="utf-8">
<title>Korvel Business Card</title>
<link href="https://fonts.googleapis.com/css2?family=Lato:wght@400;900&display=swap" rel="stylesheet">
<style>
  :root {
    --stage: #3d3d3e;
    --card: #ffffff;
    --brand: #26368f;
    --text-grey: #7d7d82;
    --faint: #eceef6;
  }
  html, body {
    margin: 0;
    padding: 0;
    width: 1200px;
    height: 810px;
    overflow: hidden;
    background: var(--stage);
    font-family: "Lato", Arial, sans-serif;
  }
  .stage {
    position: relative;
    width: 1200px;
    height: 810px;
  }
  .card {
    position: absolute;
    left: 302px;
    width: 596px;
    height: 340px;
    background: var(--card);
    border-radius: 26px;
    overflow: hidden;
  }
  .card--front { top: 45px; }
  .card--back { top: 425px; }

  .faint-circle {
    position: absolute;
    border-radius: 50%;
    background: var(--faint);
  }
  .card--front .faint-circle {
    width: 330px; height: 330px;
    left: -130px; top: 60px;
  }
  .card--back .faint-circle {
    width: 300px; height: 300px;
    right: -110px; top: -120px;
  }

  .brand-lockup {
    position: absolute;
    left: 300px;
    top: 118px;
    display: flex;
    align-items: center;
    gap: 12px;
  }
  .brand-dot {
    width: 40px; height: 40px;
    border-radius: 50%;
    background: var(--brand);
  }
  .brand-name {
    font-weight: 900;
    color: var(--brand);
    font-size: 56px;
    letter-spacing: 1px;
    line-height: 1;
  }
  .front-web {
    position: absolute;
    right: 36px;
    bottom: 30px;
    font-size: 14px;
    color: var(--text-grey);
  }

  .back-brand {
    position: absolute;
    left: 40px;
    top: 36px;
    font-size: 78px;
  }
  .person {
    position: absolute;
    left: 44px;
    top: 138px;
  }
  .person-name {
    margin: 0;
    font-weight: 900;
    font-size: 24px;
    color: var(--brand);
  }
  .person-title {
    margin: 2px 0 0;
    font-size: 15px;
    color: var(--text-grey);
  }
  .address {
    position: absolute;
    left: 44px;
    top: 210px;
    font-style: normal;
    font-size: 15px;
    line-height: 20px;
    color: var(--text-grey);
  }
  .contacts {
    position: absolute;
    left: 44px;
    top: 262px;
    margin: 0;
    padding: 0;
    list-style: none;
    font-size: 14px;
    line-height: 18px;
    color: var(--text-grey);
  }
  .contacts li {
    display: flex;
    align-items: center;
    gap: 8px;
  }
  .contacts svg { width: 13px; height: 13px; fill: var(--brand); }
  .contacts .web-domain { color: var(--brand); }
</style>
</head>
<body>
<main class="stage">
  <section class="card card--front" aria-label="Business card front">
    <div class="faint-circle"></div>
    <div class="brand-lockup">
      <span class="brand-dot"></span>
      <span class="brand-name">Korvel</span>
    </div>
    <div class="front-web">www.korvelpartsco.com</div>
  </section>

  <section class="card card--back" aria-label="Business card back">
    <div class="faint-circle"></div>
    <div class="brand-name back-brand">Korvel</div>
    <div class="person">
      <p class="person-name">Daniel Reyes</p>
      <p class="person-title">Presedent &amp; CEO</p>
    </div>
    <address class="address">4820 Harbor Mill Rd,<br>Laredo, TX 78041</address>
    <ul class="contacts">
      <li><svg viewBox="0 0 16 16"><path d="M4 1h3l1 4-2 1c1 2 2 3 4 4l1-2 4 1v3c0 1-1 2-2 2C7 14 2 9 2 3c0-1 1-2 2-2z"/></svg>(555) 318 - 4400</li>
      <li><svg viewBox="0 0 16 16"><path d="M4 1h8v4H4zM1 6h14v7h-3v-3H4v3H1zM5 11h6v4H5z"/></svg>(555) 318 - 4412</li>
      <li><svg viewBox="0 0 16 16"><path d="M1 3h14v10H1zM2 4l6 5 6-5v1L8 10 2 5z" fill-rule="evenodd"/></svg>sales@korvelpartsco.com</li>
      <li><svg viewBox="0 0 16 16"><circle cx="8" cy="8" r="6.5" fill="none" stroke="currentColor" stroke-width="1.2" style="stroke:var(--brand)"/><path d="M1.5 8h13M8 1.5c-3 3-3 10 0 13M8 1.5c3 3 3 10 0 13" fill="none" style="stroke:var(--brand)" stroke-width="1"/></svg>www.<span class="web-domain">korvelpartsco</span>.com</li>
    </ul>
  </section>
</main>
</body>
</html>
```